Business card design and logo needed - Photographer

I take photos of weddings, rodeos, snowmobiling.
Need a card to hand out to prospective clients.
Industry/Entity Type
Business
Contact Information for Business Card
Marcus Tollen Photography
Requirements
Must have
- Bold
Black or white base.
My website. www.MarcusTollen-example.com
Should not have
- camera/ lens/ aperture blades

```html
<!DOCTYPE html>
<html lang="en">
<head>
<meta charset="utf-8">
<title>Marcus Tollen Photography — Business Card</title>
<link href="https://fonts.googleapis.com/css2?family=Teko:wght@500;600&family=Rajdhani:wght@500&display=swap" rel="stylesheet">
<style>
  :root {
    --page: #d9d9d9;
    --card-ink: #1e1e1e;
    --card-edge: #ffffff;
    --type: #ffffff;
    --type-muted: #bdbdbd;
  }
  * { box-sizing: border-box; margin: 0; padding: 0; }
  html, body {
    width: 1200px;
    height: 800px;
    overflow: hidden;
    background: var(--page);
  }
  .sheet {
    width: 1200px;
    height: 800px;
    display: flex;
    align-items: center;
    justify-content: center;
    gap: 40px;
  }
  .card {
    width: 540px;
    height: 309px;
    background: var(--card-edge);
    padding: 13px;
  }
  .card__face {
    width: 100%;
    height: 100%;
    background: var(--card-ink);
    color: var(--type);
    position: relative;
  }

  /* Back side: name block left, headline right */
  .card--back .card__face {
    display: flex;
    align-items: center;
    padding: 0 34px 0 44px;
    gap: 34px;
  }
  .brand-mark {
    display: flex;
    align-items: center;
    gap: 12px;
    flex: 0 0 auto;
  }
  .brand-mark__square {
    width: 14px;
    height: 14px;
    background: var(--type);
  }
  .brand-mark__name {
    font-family: "Teko", sans-serif;
    font-weight: 600;
    font-size: 34px;
    line-height: 0.85;
    text-transform: uppercase;
    letter-spacing: 1px;
  }
  .headline {
    font-family: "Teko", sans-serif;
    font-weight: 600;
    font-size: 46px;
    line-height: 0.88;
    text-transform: uppercase;
    letter-spacing: 1px;
  }
  .headline__phone {
    display: block;
    margin-top: 10px;
    font-family: "Rajdhani", sans-serif;
    font-weight: 500;
    font-size: 13px;
    letter-spacing: 7px;
    color: var(--type-muted);
  }

  /* Front side: centred stack */
  .card--front .card__face {
    display: flex;
    flex-direction: column;
    align-items: center;
    justify-content: center;
    text-align: center;
  }
  .card--front .brand-mark { margin-bottom: 18px; }
  .card--front .brand-mark__name { font-size: 40px; }
  .front__title {
    font-family: "Teko", sans-serif;
    font-weight: 600;
    font-size: 26px;
    line-height: 1;
    text-transform: uppercase;
    letter-spacing: 1px;
  }
  .front__contact {
    margin-top: 4px;
    font-family: "Rajdhani", sans-serif;
    font-weight: 500;
    font-size: 9px;
    line-height: 1.5;
    letter-spacing: 3px;
    color: var(--type-muted);
  }
</style>
</head>
<body>
  <main class="sheet">
    <section class="card card--back" aria-label="Card back">
      <div class="card__face">
        <div class="brand-mark">
          <span class="brand-mark__square"></span>
          <span class="brand-mark__name">Marcus<br>Tollen</span>
        </div>
        <h1 class="headline">
          Marcus Tollen<br>Photography
          <span class="headline__phone">(306) 555 0148</span>
        </h1>
      </div>
    </section>

    <section class="card card--front" aria-label="Card front">
      <div class="card__face">
        <div class="brand-mark">
          <span class="brand-mark__square"></span>
          <span class="brand-mark__name">Marcus Tollen</span>
        </div>
        <p class="front__title">Marcus Tollen Photography</p>
        <p class="front__contact">(306) 555 0148<br>www.MarcusTollen-example.com</p>
      </div>
    </section>
  </main>
</body>
</html>
```